TA BRAMLEY BUSINESS CARD DESIGN PROJECT

We need to utilize our logo that was expertly created on PixelHarbor and now need to match this with a business card design.

```html
<!DOCTYPE html>
<html lang="en">
<head>
<meta charset="utf-8">
<title>TA Bramley – Business Card</title>
<link href="https://fonts.googleapis.com/css2?family=Montserrat:wght@400;500;700&display=swap" rel="stylesheet">
<style>
  :root {
    --brand-blue: #0f57ad;
    --card-black: #131313;
    --text-white: #ffffff;
    --stage: #d9d9d9;
  }
  * { margin: 0; padding: 0; box-sizing: border-box; }
  html, body { width: 1200px; height: 900px; overflow: hidden; }
  body {
    background: var(--stage);
    font-family: "Montserrat", sans-serif;
    position: relative;
  }
  .card {
    position: absolute;
    left: 340px;
    width: 520px;
    height: 300px;
    border-radius: 22px;
    overflow: hidden;
    background: var(--brand-blue);
    box-shadow: 0 10px 24px rgba(0,0,0,0.25);
  }
  .card--front { top: 130px; }
  .card--back { top: 470px; }

  .wordmark {
    font-weight: 700;
    letter-spacing: 0.12em;
    white-space: nowrap;
  }
  .card--front .wordmark {
    position: absolute;
    left: 0; right: 0; top: 50%;
    transform: translateY(-50%);
    text-align: center;
    color: var(--text-white);
    font-size: 50px;
  }

  .back-shape { position: absolute; inset: 0; }
  .card--back .wordmark {
    position: absolute;
    left: 108px; top: 132px;
    color: var(--brand-blue);
    font-size: 24px;
  }
  .divider {
    position: absolute;
    left: 302px; top: 74px;
    width: 2px; height: 160px;
    background: var(--brand-blue);
  }
  .contact {
    position: absolute;
    left: 318px; top: 70px;
    color: var(--text-white);
    font-size: 11.5px;
    line-height: 1.55;
  }
  .contact__name {
    color: var(--brand-blue);
    font-weight: 700;
    font-size: 16px;
    letter-spacing: 0.02em;
    line-height: 1.1;
  }
  .contact__role { font-size: 12px; margin-bottom: 10px; }
  .contact__list { list-style: none; }
  .contact__list li { display: flex; align-items: center; gap: 7px; }
  .contact__list svg { width: 11px; height: 11px; fill: var(--brand-blue); flex: none; }
  .contact__address { margin-top: 10px; padding-left: 18px; }
</style>
</head>
<body>
  <section class="card card--front">
    <div class="wordmark">TA BRAMLEY</div>
  </section>

  <section class="card card--back">
    <svg class="back-shape" viewBox="0 0 520 300" aria-hidden="true">
      <ellipse cx="285" cy="150" rx="225" ry="270" fill="var(--card-black)"/>
    </svg>
    <div class="wordmark">TA BRAMLEY</div>
    <div class="divider"></div>
    <div class="contact">
      <div class="contact__name">DANIEL CARTER</div>
      <div class="contact__role">Managing Director</div>
      <ul class="contact__list">
        <li><svg viewBox="0 0 12 12"><path d="M2 1h2l1 3-1.5 1a6 6 0 0 0 3.5 3.5L8 7l3 1v2a1 1 0 0 1-1 1A9 9 0 0 1 1 2a1 1 0 0 1 1-1z"/></svg>555 018 244</li>
        <li><svg viewBox="0 0 12 12"><rect x="3" y="1" width="6" height="3"/><rect x="1" y="4" width="10" height="7" rx="1"/></svg>555 018 245</li>
        <li><svg viewBox="0 0 12 12"><path d="M1 3h10v6H1z M1 3l5 4 5-4" /></svg>hello@tabramley.com</li>
        <li><svg viewBox="0 0 12 12"><circle cx="6" cy="6" r="5"/></svg>www.tabramley.com</li>
      </ul>
      <div class="contact__address">Your address, City<br>State, Zip 1234</div>
    </div>
  </section>
</body>
</html>
```